Food and Beverage Business Cards

We need business cards with logo designs for a consultant in the food and beverage industry. We specialize in helping restaurants fix operational and management problems.
Specific areas of expertise include:
-Steps of service
-Staff management tools
-Standard operating procedures
-Profit and loss management
-Inventory
-Point of sales
-Bar Menu
-Mystery shopper service
-Handling and managing suppliers

Target Market(s)

Restaurant and bar owners and managers

Industry/Entity Type

Business

Contact Information for Business Card

Mathieu Girardot
Q&T Consulting
phone: 15027390614
mathqt@sampleinbox.com

Font styles to use
Other font styles liked:
• Check out the screen shot font idea

Colors

Designer to choose colors to be used in the design.

Requirements
Must have
• Must include QR code (See attachment)
• Logo should reflect our specific focus on the drinks side of the industry.
• Areas of Expertise:
• -Service Steps
• -Staff management tools
• -S.O.P
• -P&L Management
• -Inventory
• -P.O.S
• -Bar Menu
• -Mystery Shopper Service
• -Handling and Managing Suppliers

```html
<!DOCTYPE html>
<html lang="en">
<head>
<meta charset="utf-8">
<title>Q&amp;T Consulting Business Cards</title>
<link href="https://fonts.googleapis.com/css2?family=Open+Sans:wght@400;600;700&display=swap" rel="stylesheet">
<style>
  :root {
    --backdrop: #5b4a3a;
    --card-black: #151415;
    --card-white: #f1f1f1;
    --wave-edge: #8a8a8a;
    --text-light: #ffffff;
    --text-dark: #1b1b1b;
    --badge-green: #3e7a3a;
    --badge-white: #f4f4f4;
    --badge-ring: #bdbdbd;
  }
  * { margin: 0; padding: 0; box-sizing: border-box; }
  html, body { width: 1200px; height: 960px; overflow: hidden; }
  body {
    background: var(--backdrop);
    font-family: "Open Sans", Arial, sans-serif;
    position: relative;
  }
  .card {
    position: absolute;
    width: 600px;
    height: 343px;
    overflow: hidden;
  }
  .card--front { left: 314px; top: 113px; background: var(--card-white); }
  .card--back { left: 311px; top: 472px; background: var(--card-black); color: var(--text-light); }

  .front-wave { position: absolute; inset: 0; }

  .contact {
    position: absolute;
    right: 30px;
    top: 27px;
    text-align: right;
    color: var(--text-light);
  }
  .contact__name { font-size: 18px; font-weight: 700; line-height: 26px; }
  .contact__company { font-size: 14px; font-weight: 400; line-height: 20px; letter-spacing: 0.2px; }
  .contact__line {
    font-size: 13.5px;
    line-height: 18px;
    display: flex;
    justify-content: flex-end;
    align-items: center;
    gap: 6px;
  }
  .contact__line--first { margin-top: 14px; }
  .contact__icon { width: 13px; height: 13px; fill: var(--text-light); }

  .brand-name {
    position: absolute;
    font-size: 38px;
    font-weight: 600;
    line-height: 1;
    white-space: nowrap;
  }
  .brand-name--front { left: 38px; top: 232px; color: var(--text-dark); }
  .brand-name--back { left: 0; right: 0; top: 128px; text-align: center; color: var(--text-light); }

  .badges {
    position: absolute;
    right: 20px;
    top: 17px;
    display: flex;
    gap: 6px;
  }
  .badge { width: 48px; height: 48px; border-radius: 50%; }
  .badge--green { background: var(--badge-green); }
  .badge--plain { background: var(--badge-white); border: 3px solid var(--badge-ring); }

  .expertise {
    position: absolute;
    left: 0; right: 0;
    top: 224px;
    text-align: center;
  }
  .expertise__title { font-size: 20px; font-weight: 600; line-height: 28px; margin-bottom: 4px; }
  .expertise__list { font-size: 14.5px; line-height: 20px; list-style: none; }
</style>
</head>
<body>

<section class="card card--front" aria-label="Business card front">
  <svg class="front-wave" width="600" height="343" viewBox="0 0 600 343" aria-hidden="true">
    <path d="M0,0 H600 V172 C575,232 515,242 440,207 C330,160 250,75 130,55 C70,45 30,55 0,65 Z" fill="var(--card-black)"/>
    <path d="M0,65 C30,55 70,45 130,55 C250,75 330,160 440,207 C515,242 575,232 600,172" fill="none" stroke="var(--wave-edge)" stroke-width="3"/>
  </svg>

  <div class="contact">
    <p class="contact__name">MATHIEU GIRARDOT</p>
    <p class="contact__company">Q&amp;T CONSULTING</p>
    <p class="contact__line contact__line--first">15027390614
      <svg class="contact__icon" viewBox="0 0 16 16" aria-hidden="true"><path d="M3 2h3l1.5 3.5-2 1.3a9 9 0 0 0 3.7 3.7l1.3-2L14 10v3a1 1 0 0 1-1 1A12 12 0 0 1 2 3a1 1 0 0 1 1-1z"/></svg>
    </p>
    <p class="contact__line">mathqt@sampleinbox.com
      <svg class="contact__icon" viewBox="0 0 16 16" aria-hidden="true"><path d="M1 3h14v10H1z"/><path d="M1.5 3.5 8 8l6.5-4.5" fill="none" stroke="var(--card-black)" stroke-width="1.2"/></svg>
    </p>
  </div>

  <p class="brand-name brand-name--front">Q&amp;T Consulting</p>
</section>

<section class="card card--back" aria-label="Business card back">
  <div class="badges" aria-label="Partner badges">
    <span class="badge badge--green"></span>
    <span class="badge badge--plain"></span>
    <span class="badge badge--plain"></span>
  </div>

  <p class="brand-name brand-name--back">Q&amp;T Consulting</p>

  <div class="expertise">
    <h2 class="expertise__title">Areas of Expertise</h2>
    <ul class="expertise__list">
      <li>Service Steps | Staff management tools | S.O.P | P&amp;L Management</li>
      <li>Inventory | P.O.S | Bar Menu | Mystery Shopper Service</li>
      <li>Handling and Managing Suppliers</li>
    </ul>
  </div>
</section>

</body>
</html>
```